Larkspur Talent IT Recruiting firm needs a business card design for Recruiters, Sourcers, and Account

We need business cards that allow us to change all contact info, names, titles (Recruiter, Sourcer, Account Manager, Director, CEO, etc) per person since we have three offices, in three cities, Phoenix, Austin, and Las Vegas. We do recruiting and contractors for IT positions (Developers, Architects, Software Engineers, Security Engineers, Help Desk, DBAs, PMs, Scrum Masters, etc.) Our client companies are very diverse from Meridian 100 to silicone Valley type start-ups.

So, while we what hip, techie, and quirky, it still needs to be professional. Primary color we use is blue, with silver as a secondary color.

Target Market(s)

IT, Technology

Industry/Entity Type

Business

Contact Information for Business Card

Company name: Larkspur Talent, Inc.
Website: www.larkspurtalent.example
Logos for Careerloop, Blipster, and Myriada

Name, Title, Office Number, Cell Number, email

Font styles to use
Serif
Sans Serif

Colors
0455a3
d5d5d5

Requirements
Nice to have
• The grey I selected below is not necessary - but, would like silver included. I included a card design (File 3: LTI early trial example.jpg) that I had started on. It's very rough, and not quite what we're looking for, but what we did like is the logo, big, maybe a bit faded, off center, goes out of frame, etc. Still looking for other ideas - you are the pros! But, just an idea of a design element we liked.

```html
<!DOCTYPE html>
<html lang="en">
<head>
<meta charset="utf-8">
<title>Larkspur Talent — Business Card</title>
<link rel="stylesheet" href="https://fonts.googleapis.com/css2?family=Cinzel:wght@400&family=Lato:wght@400;700&display=swap">
<style>
  :root{
    --backdrop-light:#d6dedb;
    --backdrop-dark:#97a8a6;
    --card:#0b0c0d;
    --card-edge:#16181a;
    --silver:#c9cbcc;
    --silver-dim:#a4a6a8;
    --white:#ffffff;
    --blue-bright:#3ab6f6;
    --blue-deep:#0a3af4;
    --blue-text:#2f8ee6;
    --url-grey:#5d6a6a;
    --icon-dot:#1d2022;
  }
  *{margin:0;padding:0;box-sizing:border-box}
  html,body{width:1200px;height:900px;overflow:hidden}
  body{
    position:relative;
    background:linear-gradient(200deg,var(--backdrop-light) 0%,#b9c5c2 50%,var(--backdrop-dark) 100%);
    font-family:"Lato",sans-serif;
  }
  .card{
    position:absolute;width:540px;height:312px;border-radius:16px;
    background:linear-gradient(90deg,var(--card) 0%,var(--card-edge) 100%);
    overflow:hidden;
  }
  .card--front{left:336px;top:115px}
  .card--back{left:338px;top:468px}

  .wordmark{position:absolute;font-family:"Cinzel",serif;font-weight:400;line-height:1;white-space:nowrap}
  .wordmark__top,.wordmark__bottom{display:block}
  .wordmark__bottom{text-align:right}

  .card--front .wordmark{left:26px;top:46px;color:var(--silver);font-size:35px;letter-spacing:5px}
  .card--front .wordmark__bottom{font-size:25px;letter-spacing:6px;margin-right:-6px;margin-top:0}
  .card--front .tagline{position:absolute;left:34px;top:114px;font-family:"Cinzel",serif;font-size:12.5px;letter-spacing:1.6px;color:var(--silver-dim)}

  .person{position:absolute;left:148px;top:144px}
  .person__name{font-weight:700;font-size:21px;color:var(--white)}
  .person__title{font-size:16px;color:var(--blue-text);margin-top:2px}
  .contacts{position:absolute;left:148px;top:212px;list-style:none}
  .contacts li{display:flex;align-items:center;gap:9px;font-size:16.5px;color:var(--silver);height:20.5px}
  .contacts svg{width:12px;height:12px;fill:var(--blue-text)}

  .accent{position:absolute;right:0;top:0;width:185px;height:312px}

  .card--back .wordmark{left:106px;top:88px;color:var(--white);font-size:48px;letter-spacing:10px}
  .card--back .wordmark__bottom{font-size:34px;letter-spacing:7px;margin-right:-10px;margin-top:2px}
  .card--back .tagline{position:absolute;left:0;right:0;top:186px;text-align:center;font-family:"Cinzel",serif;font-size:17px;letter-spacing:2.4px;color:var(--silver)}
  .social{position:absolute;left:0;right:0;top:228px;display:flex;justify-content:center;gap:14px;list-style:none}
  .social li{display:flex;align-items:center;gap:5px;font-size:11px;color:var(--silver-dim)}
  .social__dot{width:14px;height:14px;border-radius:50%;background:var(--icon-dot);border:1px solid #2c3033}
  .site{position:absolute;left:0;right:0;top:262px;text-align:center;font-size:14.5px;color:var(--url-grey)}
</style>
</head>
<body>

<section class="card card--front" aria-label="Business card front">
  <div class="wordmark">
    <span class="wordmark__top">LARKSPUR</span>
    <span class="wordmark__bottom">TALENT</span>
  </div>
  <p class="tagline">TALENT THAT TAKES FLIGHT</p>

  <div class="person">
    <p class="person__name">Dana Whitfield R</p>
    <p class="person__title">Designation</p>
  </div>

  <ul class="contacts">
    <li><svg viewBox="0 0 12 12" aria-hidden="true"><path d="M3 0h6a1 1 0 0 1 1 1v10a1 1 0 0 1-1 1H3a1 1 0 0 1-1-1V1a1 1 0 0 1 1-1zm0 1.5v8h6v-8z"/></svg>469 555-0182</li>
    <li><svg viewBox="0 0 12 12" aria-hidden="true"><path d="M0 4c0-2 3-3 6-3s6 1 6 3v1H9V4H3v1H0zm2 2h8l1 5H1z"/></svg>469 555-0182</li>
    <li><svg viewBox="0 0 12 12" aria-hidden="true"><path d="M0 2h12v1L6 7 0 3zm0 2.5 6 4 6-4V10H0z"/></svg>info@larkspur.example</li>
  </ul>

  <svg class="accent" viewBox="0 0 185 312" role="img" aria-label="Blue brand accent shape">
    <defs>
      <linearGradient id="accentFill" x1="0" y1="0" x2="0" y2="1">
        <stop offset="0" stop-color="#3ab6f6"/>
        <stop offset="0.6" stop-color="#2a8ff7"/>
        <stop offset="1" stop-color="#0a3af4"/>
      </linearGradient>
    </defs>
    <path d="M90 0H185V312H140C80 290 25 250 10 190 0 140 10 80 40 45 55 25 72 10 90 0Z" fill="url(#accentFill)"/>
  </svg>
</section>

<section class="card card--back" aria-label="Business card back">
  <div class="wordmark">
    <span class="wordmark__top">LARKSPUR</span>
    <span class="wordmark__bottom">TALENT</span>
  </div>
  <p class="tagline">TALENT THAT TAKES FLIGHT</p>
  <ul class="social">
    <li><span class="social__dot"></span>Myriada</li>
    <li><span class="social__dot"></span>Blipster</li>
    <li><span class="social__dot"></span>Careerloop</li>
  </ul>
  <p class="site">www.larkspurtalent.example</p>
</section>

</body>
</html>
```